I need a business card designed using the logo provided either vertical or horizontal......Harbourline Property Group is an Australian based real estate company that caters for the upper end of the market so the design of the business card "must reflect" the companies image!!
Colour combinations are optional but "must be realistic" and must be able to be accurately useable CMYK colours.
Please consider that any colours used "must be able to be used" and be suitable in following designs for "pull out banner signs" and "real estate signs".
The colours and the font in the attached designs are for example and other combinations are encouraged.
Target Market(s)
The High End of the Australian real estate market
Industry/Entity Type
Business
Contact Information for Business Card
Logo - Business Name - Director + Licensed Real Estate Agent - Mobile Number (Cell Phone) - Business Number - Fax - Email Address - Web address
Requirements
Must have
- Designs and colours (CMYK) that can easily be interpreted by an Australian printer.
Nice to have
- Some alternative ideas on colour and font..........the ones provided are ok and have been provided as an example but I am looking for alternative ideas
Should not have
- Loud, overly bright colours. Designs that do not reflect the professional standards of the business.
- Designs that look good on a computer monitor but can not be re-created on a printing press.............this is most important when it comes to shading etc.

```html
<!DOCTYPE html>
<html lang="en">
<head>
<meta charset="utf-8">
<title>Harbourline Property Group – Business Card</title>
<link rel="stylesheet" href="https://fonts.googleapis.com/css2?family=Open+Sans:wght@400;600;700&display=swap">
<style>
  :root {
    --backdrop: #e4e4e4;
    --card: #ffffff;
    --ink: #1c1c1c;
    --ink-soft: #3a3a3a;
    --gold: #b57a2c;
    --gold-light: #ead39c;
    --gold-deep: #a8681f;
    --card-shadow: rgba(0, 0, 0, 0.18);
  }
  * { box-sizing: border-box; margin: 0; padding: 0; }
  html, body {
    width: 1200px;
    height: 852px;
    overflow: hidden;
    background: var(--backdrop);
    font-family: "Open Sans", Arial, sans-serif;
    color: var(--ink);
  }
  .stage {
    width: 1200px;
    height: 852px;
    display: flex;
    align-items: center;
    justify-content: center;
    gap: 60px;
  }
  .card {
    position: relative;
    width: 520px;
    height: 300px;
    background: var(--card);
    border-radius: 18px;
    box-shadow: 0 6px 18px var(--card-shadow);
    overflow: hidden;
  }

  /* Wordmark */
  .wordmark {
    display: flex;
    align-items: center;
    gap: 12px;
  }
  .wordmark-square {
    width: 14px;
    height: 14px;
    background: var(--gold);
    flex: none;
  }
  .wordmark-name {
    font-weight: 700;
    color: var(--ink);
    text-transform: uppercase;
    letter-spacing: 0.06em;
    line-height: 1.15;
  }

  /* Front */
  .card-front {
    display: flex;
    align-items: center;
    justify-content: center;
  }
  .card-front .wordmark-name { font-size: 26px; }
  .card-front .wordmark-square { width: 20px; height: 20px; }

  /* Back */
  .card-back .wordmark {
    position: absolute;
    left: 30px;
    top: 44px;
  }
  .card-back .wordmark-name { font-size: 17px; }

  .holder {
    position: absolute;
    right: 30px;
    top: 44px;
    text-align: right;
  }
  .holder-name {
    font-size: 16px;
    font-weight: 700;
    color: var(--ink);
  }
  .holder-role {
    font-size: 11px;
    color: var(--ink-soft);
    margin-top: 1px;
  }

  .divider {
    position: absolute;
    left: 30px;
    right: 30px;
    top: 118px;
    height: 2px;
    background: var(--gold);
  }

  .contacts {
    position: absolute;
    left: 30px;
    top: 138px;
    list-style: none;
    font-size: 12.5px;
    font-weight: 600;
    color: var(--ink);
  }
  .contact-row {
    display: flex;
    align-items: center;
    gap: 22px;
    height: 24px;
  }
  .contact-item {
    display: flex;
    align-items: center;
    gap: 8px;
  }
  .contact-icon {
    width: 13px;
    height: 13px;
    fill: var(--gold);
    flex: none;
  }

  .address-band {
    position: absolute;
    left: 0;
    right: 0;
    bottom: 0;
    height: 58px;
    background: linear-gradient(90deg, var(--gold-deep) 0%, var(--gold) 30%, var(--gold-light) 62%, var(--gold) 100%);
    display: flex;
    align-items: center;
    padding-left: 30px;
    font-size: 12.5px;
    font-weight: 600;
    color: var(--ink);
  }
</style>
</head>
<body>
<main class="stage">

  <section class="card card-front" aria-label="Business card front">
    <div class="wordmark">
      <span class="wordmark-square"></span>
      <span class="wordmark-name">Harbourline<br>Property Group</span>
    </div>
  </section>

  <section class="card card-back" aria-label="Business card back">
    <div class="wordmark">
      <span class="wordmark-square"></span>
      <span class="wordmark-name">Harbourline<br>Property Group</span>
    </div>

    <div class="holder">
      <p class="holder-name">Your Long Name</p>
      <p class="holder-role">Managing Director</p>
    </div>

    <div class="divider"></div>

    <ul class="contacts">
      <li class="contact-row">
        <span class="contact-item">
          <svg class="contact-icon" viewBox="0 0 16 16" aria-hidden="true"><path d="M3.6 1.2l2.3 2.6-1.3 1.8c.9 2 2.6 3.7 4.6 4.6l1.8-1.3 2.6 2.3-1.4 2.3C7 13.6 2.4 9 1.3 2.6z"/></svg>
          00.00.00.0000
        </span>
        <span class="contact-item">
          <svg class="contact-icon" viewBox="0 0 16 16" aria-hidden="true"><path d="M4 1h6l2 2v3H4zM2 7h12a1 1 0 0 1 1 1v5H1V8a1 1 0 0 1 1-1zm2 3v4h8v-4z"/></svg>
          00.00.00.0000
        </span>
      </li>
      <li class="contact-row">
        <span class="contact-item">
          <svg class="contact-icon" viewBox="0 0 16 16" aria-hidden="true"><path d="M1 3h14v10H1zm1.5 1.2L8 8.6l5.5-4.4z"/></svg>
          yourname@yourwebsite.com
        </span>
      </li>
      <li class="contact-row">
        <span class="contact-item">
          <svg class="contact-icon" viewBox="0 0 16 16" aria-hidden="true"><path d="M8 1a7 7 0 1 0 0 14A7 7 0 0 0 8 1zm0 1.5c.8 0 1.7 1.6 2 4H6c.3-2.4 1.2-4 2-4zM2.6 6.5h2c-.1.5-.1 1-.1 1.5s0 1 .1 1.5h-2a5.5 5.5 0 0 1 0-3zm3.4 3h4c-.3 2.4-1.2 4-2 4s-1.7-1.6-2-4zm5.4 0c.1-.5.1-1 .1-1.5s0-1-.1-1.5h2a5.5 5.5 0 0 1 0 3z"/></svg>
          www.yourwebsite.com
        </span>
      </li>
    </ul>

    <footer class="address-band">Your Commercial or office address with pin code</footer>
  </section>

</main>
</body>
</html>
```